Brookvane Consulting Business Card Design

Business Card Design for Brookvane Consulting. Brookvane Consulting is a boutique consultancy based in Atlanta, GA., that specializes in marketing strategy, organization planning, and leadership development. We provide solutions for small businesses and startups as well as Vantage 300 companies.

http://brookvaneconsulting.com/

Target Market(s)

We provide solutions for small businesses and startups as well as Vantage 300 companies.

Industry/Entity Type

Consulting

Contact Information for Business Card

Two sided business card with priority on contact information, logo, tag line (Guidance to Think Bigger, Act Bolder, Grow Further)

Colors

Designer to choose colors to be used in the design.

Requirements
Must have
• contact information, logo, tag line (Guidance to Think Bigger, Act Bolder, Grow Further)
• Simple no over communication.
Nice to have
• I would like to see different placements of logo and creative use of both sides of the card
Should not have
• Do not put too much information on the card.

```html
<!DOCTYPE html>
<html lang="en">
<head>
<meta charset="utf-8">
<title>Brookvane Consulting – Business Card</title>
<link rel="stylesheet" href="https://fonts.googleapis.com/css2?family=Montserrat:wght@400;500;600&family=Kaushan+Script&display=swap">
<style>
  :root {
    --backdrop: #2b2b2b;
    --card-dark: #353535;
    --card-light: #f7f7f5;
    --ink-light: #ffffff;
    --ink-dark: #2e2e2e;
    --ink-soft: #3a3a3a;
  }
  html, body {
    margin: 0;
    padding: 0;
    width: 799px;
    height: 1200px;
    overflow: hidden;
    background: var(--backdrop);
  }
  .canvas {
    position: relative;
    width: 799px;
    height: 1200px;
  }
  .card {
    position: absolute;
    left: 80px;
    width: 640px;
    height: 366px;
    border-radius: 28px;
    box-shadow: 0 18px 40px rgba(0,0,0,0.45);
    box-sizing: border-box;
  }
  .card--front {
    top: 145px;
    background: var(--card-dark);
    display: flex;
    align-items: center;
    justify-content: center;
  }
  .card--back {
    top: 700px;
    background: var(--card-light);
    padding: 46px 0 0 44px;
  }
  .brand {
    display: flex;
    align-items: center;
    gap: 14px;
    font-family: "Montserrat", sans-serif;
    font-weight: 500;
    letter-spacing: 0.08em;
    text-transform: uppercase;
  }
  .brand__mark {
    display: block;
    border: 2px solid currentColor;
  }
  .card--front .brand {
    color: var(--ink-light);
    font-size: 34px;
  }
  .card--front .brand__mark { width: 22px; height: 22px; }
  .card--back .brand {
    color: var(--ink-dark);
    font-size: 25px;
  }
  .card--back .brand__mark { width: 16px; height: 16px; }
  .tagline {
    margin: 10px 0 0 0;
    font-family: "Montserrat", sans-serif;
    font-size: 12px;
    color: var(--ink-soft);
    letter-spacing: 0.02em;
  }
  .contact {
    position: absolute;
    left: 330px;
    top: 200px;
    font-family: "Montserrat", sans-serif;
    color: var(--ink-dark);
  }
  .contact__name {
    margin: 0 0 12px 0;
    font-family: "Kaushan Script", cursive;
    font-size: 24px;
    font-weight: 400;
  }
  .contact__line {
    margin: 0;
    font-size: 14px;
    line-height: 1.45;
  }
</style>
</head>
<body>
<main class="canvas">
  <section class="card card--front" aria-label="Card front">
    <div class="brand">
      <span class="brand__mark"></span>
      <span class="brand__name">Brookvane Consulting</span>
    </div>
  </section>

  <section class="card card--back" aria-label="Card back">
    <div class="brand">
      <span class="brand__mark"></span>
      <span class="brand__name">Brookvane Consulting</span>
    </div>
    <p class="tagline">Guidance to Think Bigger, Act Bolder, Grow Further</p>

    <div class="contact">
      <h2 class="contact__name">Marcus</h2>
      <p class="contact__line">404-555-0172</p>
      <p class="contact__line">marcus@brookvaneconsulting.com</p>
      <p class="contact__line">www.brookvaneconsulting.com</p>
    </div>
  </section>
</main>
</body>
</html>
```